full stationary design for a modern sleek design company

we are a design company that does modern minimalistic interior design works as well as other design services for high end clients.
we need a full stationary design including and not limited to (double sided business card, letter head, envelopes, documents folder...etc) that reflects the modern style design we do.
sleek modern and minimalistic is the requirements.
Updates

please use the latest attached files as there was a slight modification on the logo Added Wednesday, March 1, 2017

minor update on the logo files in JPG and PSD has been updated kindly follow the new attachments. Added Thursday, March 2, 2017

Target Market(s)

modern minimalist clients

Industry/Entity Type

Design Agency

Requirements
Must have
• the logo
Nice to have
• i like the colors in the colored 3D logo attached
Should not have
• too many colors

```html
<!DOCTYPE html>
<html lang="en">
<head>
<meta charset="utf-8">
<title>Nordline Atelier – Business Card</title>
<link rel="stylesheet" href="https://fonts.googleapis.com/css2?family=Open+Sans:wght@400;600;700&family=Josefin+Sans:wght@600&display=swap">
<style>
  :root {
    --backdrop: #5b4b3d;
    --card-white: #ffffff;
    --accent-orange: #f7941d;
    --charcoal: #333535;
    --ink: #3a3a3a;
    --text-light: #ffffff;
  }
  * { box-sizing: border-box; margin: 0; padding: 0; }
  html, body {
    width: 1200px;
    height: 987px;
    overflow: hidden;
  }
  body {
    background: var(--backdrop);
    font-family: "Open Sans", Arial, sans-serif;
    position: relative;
  }
  .card {
    position: absolute;
    left: 293px;
    width: 615px;
    height: 352px;
    border-radius: 21px;
    overflow: hidden;
    box-shadow: 0 4px 10px rgba(0,0,0,0.35);
  }
  .card-front { top: 130px; background: var(--card-white); }
  .card-back { top: 505px; background: var(--charcoal); }

  .front-shapes { position: absolute; inset: 0; }

  .brand {
    position: absolute;
    display: flex;
    align-items: center;
    font-family: "Josefin Sans", "Open Sans", sans-serif;
    font-weight: 600;
    white-space: nowrap;
    line-height: 1;
  }
  .brand-mark { display: block; flex: none; background: var(--accent-orange); }
  .brand-front {
    left: 28px; top: 167px;
    font-size: 16px;
    letter-spacing: 0.06em;
    color: var(--ink);
    gap: 8px;
  }
  .brand-front .brand-mark { width: 18px; height: 18px; }
  .brand-back {
    left: 0; right: 0; top: 156px;
    justify-content: center;
    font-size: 32px;
    letter-spacing: 0.08em;
    color: var(--accent-orange);
    gap: 14px;
  }
  .brand-back .brand-mark { width: 30px; height: 30px; }

  .contact {
    position: absolute;
    right: 34px;
    top: 70px;
    text-align: right;
    color: var(--text-light);
    font-size: 16px;
    line-height: 1.4;
  }
  .contact-name {
    color: var(--ink);
    font-weight: 700;
    font-size: 21px;
    line-height: 1.1;
  }
  .contact-title { margin-bottom: 10px; }
  .contact-address { margin-bottom: 7px; line-height: 1.4; }
  .contact-line {
    display: flex;
    justify-content: flex-end;
    align-items: center;
    gap: 7px;
    height: 23.5px;
  }
  .contact-icon { width: 15px; height: 15px; flex: none; }
</style>
</head>
<body>

<section class="card card-front">
  <svg class="front-shapes" width="615" height="352" viewBox="0 0 615 352" aria-hidden="true">
    <g fill="var(--charcoal)">
      <circle cx="480" cy="175" r="189"/>
      <rect x="480" y="0" width="135" height="352"/>
    </g>
    <g fill="var(--card-white)">
      <circle cx="480" cy="175" r="182"/>
      <rect x="480" y="0" width="135" height="352"/>
    </g>
    <g fill="var(--accent-orange)">
      <circle cx="480" cy="175" r="177"/>
      <rect x="480" y="0" width="135" height="352"/>
    </g>
  </svg>

  <div class="brand brand-front">
    <span class="brand-mark"></span>
    <span class="brand-name">NORDLINE ATELIER</span>
  </div>

  <div class="contact">
    <p class="contact-name">MARA LIND</p>
    <p class="contact-title">CEO&amp;Founder</p>
    <p class="contact-address">214 Alder Court<br>Portland, Oregon 97201</p>
    <p class="contact-line">(503) 555 0142
      <svg class="contact-icon" viewBox="0 0 16 16" aria-hidden="true"><path fill="var(--ink)" d="M3.6 1.2l2.3 2.6-1.3 1.9c.9 2 2.4 3.5 4.4 4.5l1.9-1.3 2.6 2.3-1.4 2.3C7.5 14.2 1.8 8.5 1.3 2.6z"/></svg>
    </p>
    <p class="contact-line">(503) 555 0187
      <svg class="contact-icon" viewBox="0 0 16 16" aria-hidden="true"><rect x="3.5" y="0.8" width="9" height="14.4" rx="1.5" fill="var(--ink)"/><rect x="5" y="2.6" width="6" height="9.4" fill="var(--accent-orange)"/></svg>
    </p>
    <p class="contact-line">mara@nordline.com
      <svg class="contact-icon" viewBox="0 0 16 16" aria-hidden="true"><rect x="1" y="3.5" width="14" height="9" fill="var(--ink)"/><path d="M1.5 4l6.5 5 6.5-5" fill="none" stroke="var(--accent-orange)" stroke-width="1"/></svg>
    </p>
    <p class="contact-line">www.nordline.com
      <svg class="contact-icon" viewBox="0 0 16 16" aria-hidden="true"><circle cx="8" cy="8" r="7" fill="var(--ink)"/><path d="M1.5 8h13M8 1.2c-2.5 3-2.5 10.6 0 13.6M8 1.2c2.5 3 2.5 10.6 0 13.6" fill="none" stroke="var(--accent-orange)" stroke-width="0.9"/></svg>
    </p>
  </div>
</section>

<section class="card card-back">
  <div class="brand brand-back">
    <span class="brand-mark"></span>
    <span class="brand-name">NORDLINE ATELIER</span>
  </div>
</section>

</body>
</html>
```